Photojournalism/photography business needs a simple, timeless & professional letterhead design

We need a letterhead design for photography/photojournalism business called 'plunq', no capitals.

The letterhead needs to be:
- simple
- professional
- timeless
- easy to read
- consists of at least 2 colors to make it stands out.

We do mainly editorial photography, photo articles for various publications, travel, businesses, as well as people such as family and kids.

The final design should communicate professionalism, easy identification, attention grabbing, even if it has to be found among a stack of various papers on the clients' desks.

Target Market(s)

Various publications.

Industry/Entity Type

Business

Requirements
Must have
• Please use the logo attached.

```html
<!DOCTYPE html>
<html lang="en">
<head>
<meta charset="utf-8">
<title>plunq letterhead</title>
<link rel="stylesheet" href="https://fonts.googleapis.com/css2?family=Didact+Gothic&display=swap">
<style>
  :root {
    --backdrop: #e6e4e1;
    --paper: #ffffff;
    --paper-glow: #f3f3f5;
    --ink: #3a3b3d;
    --mark-faint: #efeff1;
    --mark-fainter: #f4f4f6;
  }
  * { margin: 0; padding: 0; box-sizing: border-box; }
  html, body {
    width: 1200px;
    height: 1181px;
    overflow: hidden;
    background: var(--backdrop);
  }
  .letterhead {
    position: absolute;
    left: 272px;
    top: 122px;
    width: 656px;
    height: 928px;
    background: radial-gradient(circle at 50% 58%, var(--paper-glow) 0%, var(--paper) 55%);
    box-shadow: 0 4px 14px rgba(0, 0, 0, 0.18);
    font-family: "Didact Gothic", "Century Gothic", sans-serif;
    color: var(--ink);
  }
  .brand-name {
    position: absolute;
    top: 22px;
    left: 0;
    width: 100%;
    text-align: center;
    font-size: 72px;
    line-height: 1;
    letter-spacing: -1px;
    color: var(--ink);
  }
  .backdrop-mark {
    position: absolute;
    left: 140px;
    top: 290px;
    width: 400px;
    height: 400px;
  }
  .footer-details {
    position: absolute;
    bottom: 10px;
    left: 0;
    width: 100%;
    text-align: center;
    font-size: 21px;
    color: #222;
  }
</style>
</head>
<body>
  <main class="letterhead">
    <h1 class="brand-name">plunq</h1>

    <svg class="backdrop-mark" viewBox="0 0 400 400" aria-hidden="true">
      <rect class="mark-back" x="70" y="70" width="270" height="250" fill="var(--mark-fainter)" transform="rotate(-8 205 195)"/>
      <rect class="mark-front" x="60" y="60" width="280" height="280" fill="var(--mark-faint)" transform="rotate(-24 200 200)"/>
    </svg>

    <p class="footer-details">Details if required</p>
  </main>
</body>
</html>
```